Ridgeline Journeys business card

please see website
www.ridgelinejourneys.comau

info needed on card
Curtis Halvey
Ph
email
Adventure Riding GPS trails

please use my logo and colours off my site

Curtis Halvey
curtis@ridgelinejourneys.com

```html
<!DOCTYPE html>
<html lang="en">
<head>
<meta charset="utf-8">
<title>Ridgeline Journeys business card</title>
<link href="https://fonts.googleapis.com/css2?family=Arimo:wght@400;700&display=swap" rel="stylesheet">
<style>
  :root {
    --backdrop: #e6e4df;
    --card-white: #fbfbfb;
    --brand-yellow: #e8df3d;
    --ink: #161616;
    --mark-yellow: #f1dc2a;
  }
  html, body {
    margin: 0;
    width: 1200px;
    height: 902px;
    overflow: hidden;
    background: var(--backdrop);
    font-family: "Arimo", Arial, sans-serif;
  }
  .business-card {
    position: absolute;
    left: 250px;
    width: 700px;
    height: 400px;
    background: var(--card-white);
    box-shadow: 0 8px 24px rgba(0,0,0,0.16);
    overflow: hidden;
  }
  .card-back { top: 34px; }
  .card-front { top: 468px; }

  .brand-name {
    margin: 0;
    font-weight: 700;
    text-transform: uppercase;
    color: var(--ink);
    letter-spacing: 1px;
    line-height: 1.02;
  }
  .brand-dot {
    border-radius: 50%;
    background: var(--mark-yellow);
    flex: none;
  }

  /* back side: centred brand */
  .back-lockup {
    position: absolute;
    inset: 0;
    display: flex;
    align-items: center;
    justify-content: center;
    gap: 34px;
  }
  .back-lockup .brand-dot { width: 130px; height: 130px; }
  .back-lockup .brand-name { font-size: 60px; }

  /* front side */
  .card-swoosh {
    position: absolute;
    inset: 0;
    width: 100%;
    height: 100%;
  }
  .front-lockup {
    position: absolute;
    left: 160px;
    top: 62px;
    display: flex;
    align-items: center;
    gap: 24px;
  }
  .front-lockup .brand-dot { width: 78px; height: 78px; }
  .front-lockup .brand-name { font-size: 45px; }
  .holder-name {
    position: absolute;
    left: 28px;
    top: 322px;
    margin: 0;
    font-size: 34px;
    font-weight: 400;
    color: var(--ink);
  }
  .contact-divider {
    position: absolute;
    left: 294px;
    top: 262px;
    width: 2px;
    height: 98px;
    background: var(--ink);
  }
  .contact-list {
    position: absolute;
    left: 310px;
    top: 268px;
    margin: 0;
    padding: 0;
    list-style: none;
    color: var(--ink);
    font-size: 19px;
  }
  .contact-list li {
    display: flex;
    align-items: center;
    gap: 12px;
    height: 36px;
  }
  .contact-icon {
    width: 18px;
    height: 18px;
    flex: none;
  }
</style>
</head>
<body>
  <section class="business-card card-back">
    <div class="back-lockup">
      <span class="brand-dot"></span>
      <h2 class="brand-name">Ridgeline<br>Journeys</h2>
    </div>
  </section>

  <section class="business-card card-front">
    <svg class="card-swoosh" viewBox="0 0 1000 572" preserveAspectRatio="none" aria-hidden="true">
      <path d="M0,392 C350,392 650,222 1000,132 L1000,572 L0,572 Z" fill="var(--ink)"/>
      <path d="M0,420 C350,420 650,250 1000,160 L1000,572 L0,572 Z" fill="var(--brand-yellow)"/>
    </svg>

    <div class="front-lockup">
      <span class="brand-dot"></span>
      <h1 class="brand-name">Ridgeline<br>Journeys</h1>
    </div>

    <p class="holder-name">Curtis Halvey</p>
    <span class="contact-divider"></span>

    <ul class="contact-list">
      <li>
        <svg class="contact-icon" viewBox="0 0 26 26" aria-label="email">
          <rect x="1" y="1" width="24" height="24" rx="3" fill="var(--ink)"/>
          <rect x="5" y="8" width="16" height="11" fill="none" stroke="var(--brand-yellow)" stroke-width="2"/>
          <path d="M5,8 L13,14 L21,8" fill="none" stroke="var(--brand-yellow)" stroke-width="2"/>
        </svg>
        <span>curtis@ridgelinejourneys.com</span>
      </li>
      <li>
        <svg class="contact-icon" viewBox="0 0 26 26" aria-label="website">
          <rect x="1" y="1" width="24" height="24" rx="3" fill="var(--ink)"/>
          <circle cx="13" cy="13" r="8" fill="none" stroke="var(--brand-yellow)" stroke-width="2"/>
          <path d="M5,13 H21 M13,5 C9,9 9,17 13,21 M13,5 C17,9 17,17 13,21" fill="none" stroke="var(--brand-yellow)" stroke-width="1.6"/>
        </svg>
        <span>www.ridgelinejourneys.com.au</span>
      </li>
    </ul>
  </section>
</body>
</html>
```